Web Developer Needs a Business Card Design

I need a personal business card design that represents me as a web developer for potential employers. I would like the background to be a dark color on the front for contrast with my logo and name. The back will have all my information along with a smaller version of the logo. I want something with a modern look and feel, not too conservative. This will be used for potential employers and freelance work.

Industry/Entity Type

Business

Contact Information for Business Card

Front should have my logo and name. The back should have all my personal information which would include: name: Tom Varulek, phone: 570-614-3098, email: tomvarulek@quillbox.net, website url: www.tomvarulek.net, logo, web developer.

Font styles to use
Sans Serif

Requirements
Must have
• Must include my logo. The color palette base color will be the logo color.

```html
<!DOCTYPE html>
<html lang="en">
<head>
<meta charset="utf-8">
<title>Tom Varulek – Business Card</title>
<link rel="stylesheet" href="https://fonts.googleapis.com/css2?family=Lato:wght@400;700;900&family=Questrial&display=swap">
<style>
  :root {
    --teal: #5fc2ab;
    --teal-dark: #49ad96;
    --ink: #1d1d1d;
    --band: #141414;
    --paper: #ffffff;
    --stage: #e9e7e3;
  }
  * { box-sizing: border-box; margin: 0; padding: 0; }
  html, body { width: 1200px; height: 913px; overflow: hidden; }
  body {
    background: var(--stage);
    font-family: "Lato", sans-serif;
    position: relative;
  }
  .card {
    position: absolute;
    width: 525px;
    height: 300px;
    background: var(--paper);
    box-shadow: 0 6px 18px rgba(0,0,0,.18);
    overflow: hidden;
  }
  .card--contact { left: 50px; top: 306px; }
  .card--identity { left: 625px; top: 306px; }

  /* contact side */
  .accent-band {
    position: absolute; left: 14px; top: 0; bottom: 0; width: 190px;
    background: linear-gradient(180deg, var(--teal) 0%, var(--teal-dark) 100%);
  }
  .info-band {
    position: absolute; left: 196px; right: 0; top: 38px; height: 132px;
    background: linear-gradient(180deg, #2a2a2a 0%, var(--band) 100%);
  }
  .mark {
    position: absolute; border-radius: 50%;
    display: flex; align-items: center; justify-content: center;
  }
  .card--contact .mark {
    left: 133px; top: 98px; width: 126px; height: 126px;
    background: var(--paper);
    border: 7px solid var(--paper);
    box-shadow: inset 0 0 0 5px var(--teal);
  }
  .mark__name {
    color: var(--teal); font-family: "Lato", sans-serif; font-weight: 700;
    font-size: 15px; text-align: center; line-height: 1.15;
  }
  .contact {
    position: absolute; right: 20px; top: 50px;
    text-align: right; color: var(--paper);
  }
  .contact__name { font-weight: 900; font-size: 21px; letter-spacing: .5px; line-height: 1.1; }
  .contact__role { color: var(--teal); font-weight: 700; font-size: 13px; letter-spacing: .5px; margin-bottom: 8px; }
  .contact__line {
    font-size: 13px; line-height: 19px;
    display: flex; justify-content: flex-end; align-items: center; gap: 6px;
  }
  .contact__line svg { width: 12px; height: 12px; flex: none; }

  /* identity side */
  .card--identity .mark {
    left: 211px; top: 62px; width: 104px; height: 104px;
    border: 6px solid var(--teal);
  }
  .identity__name {
    position: absolute; left: 0; right: 0; top: 186px; text-align: center;
    font-family: "Questrial", sans-serif; font-size: 31px; letter-spacing: 2px; color: var(--ink);
  }
  .identity__role {
    position: absolute; left: 0; right: 0; top: 232px; text-align: center;
    font-size: 15px; color: var(--ink); letter-spacing: .3px;
  }
</style>
</head>
<body>
  <section class="card card--contact">
    <div class="accent-band"></div>
    <div class="info-band"></div>
    <div class="mark"><span class="mark__name">Tom<br>Varulek</span></div>
    <div class="contact">
      <p class="contact__name">TOM VARULEK</p>
      <p class="contact__role">WEB DEVELOPER</p>
      <p class="contact__line">570-614-3098
        <svg viewBox="0 0 24 24" fill="var(--teal)"><path d="M6.6 10.8a15.1 15.1 0 0 0 6.6 6.6l2.2-2.2a1 1 0 0 1 1-.25 11.4 11.4 0 0 0 3.6.57 1 1 0 0 1 1 1V20a1 1 0 0 1-1 1A17 17 0 0 1 3 4a1 1 0 0 1 1-1h3.5a1 1 0 0 1 1 1c0 1.25.2 2.45.57 3.57a1 1 0 0 1-.25 1z"/></svg>
      </p>
      <p class="contact__line">tomvarulek@quillbox.net
        <svg viewBox="0 0 24 24" fill="none" stroke="var(--teal)" stroke-width="2.4"><rect x="3" y="5" width="18" height="14" rx="1"/><path d="M3 6l9 7 9-7"/></svg>
      </p>
      <p class="contact__line">www.tomvarulek.net
        <svg viewBox="0 0 24 24" fill="none" stroke="var(--teal)" stroke-width="2"><circle cx="12" cy="12" r="9"/><path d="M3 12h18M12 3c3 3 3 15 0 18M12 3c-3 3-3 15 0 18"/></svg>
      </p>
    </div>
  </section>

  <section class="card card--identity">
    <div class="mark"><span class="mark__name">Tom<br>Varulek</span></div>
    <p class="identity__name">TOM VARULEK</p>
    <p class="identity__role">Front-End Developer</p>
  </section>
</body>
</html>
```